PlumVesta screens tidy up

We would like advice on how to better present the following home page and overview pages.

The existing website is functional, but the pages don't appear professionals and pleasing to the eye. We would specifically like feedback on alignment and padding of icons and text to make the screen more appealing and polished.

We are following the quartzline design system.

1 page

Sans Serif
• IBM Plex, Poppins

```html
<!DOCTYPE html>
<html lang="en">
<head>
<meta charset="utf-8">
<title>PlumVesta – Home and Overview</title>
<link rel="stylesheet" href="https://fonts.googleapis.com/css2?family=Nunito+Sans:wght@400;600;700&display=swap">
<style>
:root{
  --stage:#9fa0a4;
  --orange:#f7a23b;
  --orange-dark:#ef8d1e;
  --peach:#f9dcb6;
  --peach-soft:#f6ebe1;
  --sidebar:#f3f3f3;
  --tile:#f5f4f4;
  --ink:#1d1d1f;
  --muted:#4a4a4a;
  --line:#dcdcdc;
  --white:#ffffff;
}
*{box-sizing:border-box;margin:0;padding:0}
html,body{width:717px;height:1200px;overflow:hidden;background:var(--stage)}
body{font-family:"Nunito Sans",Arial,sans-serif;color:var(--ink)}
.stage{position:absolute;left:0;top:0;width:1484px;height:2484px;transform:scale(.4832);transform-origin:0 0}
.screen{position:absolute;left:84px;width:1316px;background:var(--white);overflow:hidden}
.screen--home{top:76px;height:1274px}
.screen--overview{top:1416px;height:962px}
.abs{position:absolute}
.topbar{left:0;top:0;width:1316px;height:74px;background:var(--white);box-shadow:0 2px 6px rgba(0,0,0,.05);z-index:2}
.brand{left:22px;top:14px;display:flex;align-items:center;gap:10px}
.brand-dot{width:40px;height:40px;border-radius:50%;background:var(--orange)}
.brand-name{font-size:25px;font-weight:700;color:var(--ink)}
.page-title{left:281px;top:24px;font-size:21px;font-weight:600}
.crumb{left:282px;top:14px;font-size:16px;color:var(--muted)}
.crumb + .page-title{top:34px;font-size:22px;font-weight:700}
.user-badge{left:1186px;top:14px;width:40px;height:44px}
.user-name{left:1237px;top:12px;font-size:16px}
.logout{left:1238px;top:38px;width:56px;height:20px;background:var(--orange);color:#fff;font-size:12px;text-align:center;line-height:20px}
.sidebar{left:0;top:74px;width:237px;bottom:0;background:var(--sidebar)}
.nav-item{position:absolute;left:20px;width:206px;display:flex;align-items:center;gap:12px;font-size:14.5px;height:24px}
.nav-item svg{width:16px;height:16px;flex:none}
.nav-item .end{position:absolute;right:0;width:18px;height:18px}
.nav-divider{position:absolute;left:12px;width:214px;height:1px;background:var(--line)}
.nav-item--active{color:var(--orange-dark);font-weight:600}
.nav-band{position:absolute;left:0;width:237px;height:52px;background:var(--orange)}
.nav-sub{position:absolute;left:0;width:237px;height:176px;background:var(--peach)}
.nav-sub--soft{background:var(--peach-soft)}
.nav-sub-hl{position:absolute;left:0;width:237px;height:40px;background:var(--peach)}
.sub-link{position:absolute;left:42px;font-size:13px;display:flex;align-items:center;gap:8px}
.sub-link::before{content:"";border-left:4px solid var(--ink);border-top:3px solid transparent;border-bottom:3px solid transparent}
.section-label{position:absolute;font-size:16px;font-weight:600}
.card{position:absolute;background:var(--white);box-shadow:0 0 8px rgba(0,0,0,.07)}
.card--accent{border-left:5px solid var(--orange)}
.tile{position:absolute;background:var(--tile);width:204px}
.tile .icon{position:absolute;left:77px;width:52px;height:52px;border-radius:50%;background:var(--orange);display:flex;align-items:center;justify-content:center}
.tile .num{position:absolute;left:0;width:100%;text-align:center;font-size:28px}
.circle-icon{position:absolute;border-radius:50%;background:var(--orange);display:flex;align-items:center;justify-content:center}
.btn{position:absolute;background:var(--orange);color:#fff;font-size:14px;display:flex;align-items:center;justify-content:center}
.camp-card{position:absolute;top:807px;width:302px;height:361px;background:var(--tile);text-align:center}
.camp-card h3{position:absolute;top:140px;width:100%;font-size:19px;font-weight:600}
.camp-card p{position:absolute;top:170px;width:100%;font-size:13px}
.camp-stat{position:absolute;left:25px;top:214px;width:257px;height:72px;background:#fff;display:flex;align-items:center}
.camp-stat .n{width:56px;text-align:center;font-size:30px;border-right:1px solid #ccc;line-height:52px}
.camp-stat .t{padding-left:17px;text-align:left;font-size:15px;line-height:21px}
.camp-card .since{position:absolute;top:313px;width:100%;font-size:13px}
.copyright{position:absolute;left:237px;right:0;text-align:center;font-size:12px;color:var(--muted)}
.org-box{position:absolute;width:66px;height:58px;background:var(--tile);font-size:22px;display:flex;align-items:center;justify-content:center}
.org-text{position:absolute;font-size:14.5px;line-height:19px}
.org-text small{display:block;font-size:13px;color:var(--muted);margin-top:4px}
</style>
</head>
<body>
<svg width="0" height="0" style="position:absolute">
  <defs>
    <linearGradient id="barFill" x1="0" y1="0" x2="0" y2="1">
      <stop offset="0" stop-color="#a98ff5"/><stop offset="1" stop-color="#46b1ec"/>
    </linearGradient>
    <symbol id="i-home" viewBox="0 0 16 16"><path d="M2 7.5 8 2l6 5.5V14H10v-4H6v4H2z" fill="none" stroke="currentColor" stroke-width="1.2"/></symbol>
    <symbol id="i-bell" viewBox="0 0 16 16"><path d="M4 11V7a4 4 0 0 1 8 0v4l1.5 1.5h-11zM6.5 14h3" fill="none" stroke="currentColor" stroke-width="1.2"/></symbol>
    <symbol id="i-gear" viewBox="0 0 16 16"><circle cx="8" cy="8" r="2.2" fill="none" stroke="currentColor" stroke-width="1.2"/><circle cx="8" cy="8" r="5.5" fill="none" stroke="currentColor" stroke-width="1.2" stroke-dasharray="2 1.5"/></symbol>
    <symbol id="i-horn" viewBox="0 0 16 16"><path d="M2 6h3l6-3v10L5 10H2zM5 10l1 4h2" fill="none" stroke="currentColor" stroke-width="1.2"/></symbol>
    <symbol id="i-doc" viewBox="0 0 16 16"><path d="M3.5 1.5h6l3 3v10h-9zM6 7h4M6 9.5h4M6 12h3" fill="none" stroke="currentColor" stroke-width="1.2"/></symbol>
    <symbol id="i-edit" viewBox="0 0 16 16"><path d="M2 3h7M2 3v11h11V8M7 10l7-7-1.5-1.5-7 7L5 11z" fill="none" stroke="currentColor" stroke-width="1.2"/></symbol>
    <symbol id="i-plus" viewBox="0 0 18 18"><path d="M9 2v14M2 9h14" stroke="currentColor" stroke-width="1.4"/></symbol>
    <symbol id="i-up" viewBox="0 0 18 18"><path d="M3 12l6-6 6 6" fill="none" stroke="currentColor" stroke-width="1.6"/></symbol>
    <symbol id="i-down" viewBox="0 0 18 18"><path d="M3 6l6 6 6-6" fill="none" stroke="currentColor" stroke-width="1.6"/></symbol>
    <symbol id="i-tick" viewBox="0 0 32 32"><circle cx="16" cy="16" r="12" fill="none" stroke="#fff" stroke-width="2"/><path d="M10 16l4.5 4.5L23 11" fill="none" stroke="#fff" stroke-width="2.2"/></symbol>
    <symbol id="i-file" viewBox="0 0 32 32"><path d="M9 5h10l5 5v17H9zM12 13h9M12 17h9M12 21h9" fill="none" stroke="#fff" stroke-width="1.6"/></symbol>
    <symbol id="i-campaign" viewBox="0 0 48 48"><rect x="7" y="9" width="28" height="26" rx="2" fill="none" stroke="#fff" stroke-width="2"/><path d="M7 14h28" stroke="#fff" stroke-width="2"/><circle cx="17" cy="23" r="4" fill="none" stroke="#fff" stroke-width="2"/><path d="M24 21h7M24 25h7M12 30h14" stroke="#fff" stroke-width="2"/><circle cx="36" cy="34" r="7" fill="var(--orange)" stroke="#fff" stroke-width="2"/></symbol>
    <symbol id="i-people" viewBox="0 0 32 32"><circle cx="10" cy="12" r="3" fill="none" stroke="#fff" stroke-width="1.6"/><circle cx="16" cy="9" r="3" fill="none" stroke="#fff" stroke-width="1.6"/><circle cx="22" cy="12" r="3" fill="none" stroke="#fff" stroke-width="1.6"/><rect x="5" y="17" width="22" height="8" rx="3" fill="none" stroke="#fff" stroke-width="1.6"/></symbol>
    <symbol id="i-tree" viewBox="0 0 32 32"><rect x="12" y="4" width="8" height="7" fill="none" stroke="#fff" stroke-width="1.6"/><path d="M16 11v5M7 16h18M7 16v4M16 16v4M25 16v4" fill="none" stroke="#fff" stroke-width="1.6"/><rect x="4" y="20" width="6" height="6" fill="none" stroke="#fff" stroke-width="1.6"/><rect x="13" y="20" width="6" height="6" fill="none" stroke="#fff" stroke-width="1.6"/><rect x="22" y="20" width="6" height="6" fill="none" stroke="#fff" stroke-width="1.6"/></symbol>
    <symbol id="i-cog" viewBox="0 0 32 32"><circle cx="16" cy="16" r="4" fill="none" stroke="#fff" stroke-width="1.8"/><circle cx="16" cy="16" r="10" fill="none" stroke="#fff" stroke-width="1.8" stroke-dasharray="3.5 2.5"/></symbol>
    <symbol id="i-alert" viewBox="0 0 32 32"><path d="M9 21v-7a7 7 0 0 1 14 0v7l2 2H7zM13 26h6" fill="none" stroke="#fff" stroke-width="1.8"/></symbol>
    <symbol id="i-user" viewBox="0 0 40 44"><path d="M20 1 38 11v22L20 43 2 33V11z" fill="var(--orange)"/><circle cx="20" cy="17" r="6" fill="none" stroke="#fff" stroke-width="2"/><path d="M9 33c2-6 6-8 11-8s9 2 11 8" fill="none" stroke="#fff" stroke-width="2"/></symbol>
  </defs>
</svg>

<div class="stage">

<!-- Home screen -->
<section class="screen screen--home">
  <header class="abs topbar">
    <div class="abs brand"><span class="brand-dot"></span><span class="brand-name">PlumVesta</span></div>
    <div class="abs page-title">Home</div>
    <svg class="abs user-badge"><use href="#i-user"/></svg>
    <div class="abs user-name">Marcus</div>
    <div class="abs logout">Logout</div>
  </header>

  <nav class="abs sidebar">
    <div class="nav-item nav-item--active" style="top:28px"><svg><use href="#i-home"/></svg>Home</div>
    <div class="nav-divider" style="top:65px"></div>
    <div class="nav-item" style="top:81px"><svg><use href="#i-bell"/></svg>All Alerts</div>
    <div class="nav-divider" style="top:117px"></div>
    <div class="nav-item" style="top:134px"><svg><use href="#i-gear"/></svg>Manage</div>
    <div class="nav-divider" style="top:170px"></div>
    <div class="nav-item" style="top:186px"><svg><use href="#i-horn"/></svg>Campaigns<svg class="end"><use href="#i-plus"/></svg></div>
    <div class="nav-band" style="top:224px"></div>
    <div class="nav-item" style="top:238px"><svg><use href="#i-doc"/></svg>My custom Campaign<svg class="end"><use href="#i-up"/></svg></div>
    <div class="nav-sub" style="top:276px"></div>
    <div class="sub-link" style="top:292px">Overview</div>
    <div class="sub-link" style="top:324px">Files &amp; Honey Tokens</div>
    <div class="sub-link" style="top:355px">Resources</div>
    <div class="sub-link" style="top:387px">Alerts</div>
    <div class="sub-link" style="top:418px">Settings</div>
    <div class="nav-item" style="top:465px"><svg><use href="#i-edit"/></svg>Default Campaign<svg class="end"><use href="#i-down"/></svg></div>
  </nav>

  <div class="section-label" style="left:281px;top:112px">Teamspace</div>
  <div class="card card--accent" style="left:281px;top:150px;width:996px;height:98px">
    <div class="abs" style="left:29px;top:18px;font-size:25px">Default</div>
    <div class="abs" style="left:29px;top:56px;font-size:13px">The default client is created as a part of your user account</div>
  </div>

  <div class="section-label" style="left:281px;top:288px">Subscription Overview</div>
  <div class="card" style="left:281px;top:325px;width:474px;height:367px">
    <svg class="abs" style="left:0;top:0" width="474" height="367" viewBox="0 0 474 367" font-family="Nunito Sans, sans-serif" font-size="12" fill="#8a8fa0">
      <g stroke="#e4e6ea">
        <line x1="75" y1="56" x2="425" y2="56"/><line x1="75" y1="106" x2="425" y2="106"/>
        <line x1="75" y1="155" x2="425" y2="155"/><line x1="75" y1="204" x2="425" y2="204"/>
      </g>
      <text x="52" y="50">400</text><text x="52" y="100">300</text><text x="52" y="149">200</text><text x="52" y="198">100</text><text x="52" y="248">0</text>
      <g fill="url(#barFill)">
        <rect x="108" y="105" width="18" height="148" rx="2"/><rect x="157" y="78" width="18" height="175" rx="2"/>
        <rect x="206" y="121" width="18" height="132" rx="2"/><rect x="255" y="78" width="18" height="175" rx="2"/>
        <rect x="304" y="95" width="18" height="158" rx="2"/><rect x="353" y="78" width="18" height="175" rx="2"/>
        <rect x="402" y="121" width="18" height="132" rx="2" opacity=".3"/>
      </g>
      <text x="62" y="272">10</text><text x="110" y="272">15</text><text x="159" y="272">20</text><text x="208" y="272">25</text>
      <text x="257" y="272">30</text><text x="306" y="272">35</text><text x="355" y="272">40</text><text x="404" y="272">45</text>
    </svg>
    <div class="abs" style="left:52px;top:301px;font-size:19px">Starter pack usage</div>
    <div class="abs" style="left:246px;top:306px;font-size:13px">0 files active out of 10 allowed</div>
  </div>

  <div class="section-label" style="left:802px;top:288px">Files &amp;Honey Takens</div>
  <div class="card" style="left:802px;top:325px;width:475px;height:367px">
    <div class="abs" style="left:27px;top:24px;font-size:16px">Statistics</div>
  </div>
  <div class="tile" style="left:831px;top:393px;height:175px"><div class="icon" style="top:38px"><svg width="32" height="32"><use href="#i-tick"/></svg></div><div class="num" style="top:104px">0</div></div>
  <div class="tile" style="left:1051px;top:393px;height:175px"><div class="icon" style="top:38px"><svg width="32" height="32"><use href="#i-file"/></svg></div><div class="num" style="top:104px">30</div></div>

  <div class="section-label" style="left:281px;top:737px">Campaigns</div>
  <div class="btn" style="left:1153px;top:727px;width:123px;height:34px;font-size:13px">New Campaign</div>
  <div class="card" style="left:281px;top:780px;width:996px;height:420px"></div>

  <article class="camp-card" style="left:305px">
    <div class="circle-icon" style="left:108px;top:30px;width:86px;height:86px"><svg width="54" height="54"><use href="#i-campaign"/></svg></div>
    <h3>My Custom Campaign</h3>
    <p>This is my custom campaign for finding!</p>
    <div class="camp-stat"><span class="n">0</span><span class="t">Active<br>Files and HoneyTokens</span></div>
    <div class="since">Active Since : July 25, 2023 | 13:12</div>
  </article>
  <article class="camp-card" style="left:625px">
    <div class="circle-icon" style="left:108px;top:30px;width:86px;height:86px"><svg width="54" height="54"><use href="#i-campaign"/></svg></div>
    <h3>My Custom Campaign</h3>
    <p>Define your own mission, or combine difference.</p>
    <div class="camp-stat"><span class="n">0</span><span class="t">Active<br>Files and HoneyTokens</span></div>
    <div class="since">Active Since : July 25, 2023 | 13:12</div>
  </article>

  <div class="copyright" style="top:1231px">Copyright © 2023 All Rights Reserved</div>
</section>

<!-- Campaign overview screen -->
<section class="screen screen--overview">
  <header class="abs topbar">
    <div class="abs brand"><span class="brand-dot"></span><span class="brand-name">PlumVesta</span></div>
    <div class="abs crumb">My Custom Campaign</div>
    <div class="abs page-title">Overview</div>
    <svg class="abs user-badge"><use href="#i-user"/></svg>
    <div class="abs user-name">Marcus</div>
    <div class="abs logout">Logout</div>
  </header>

  <nav class="abs sidebar">
    <div class="nav-item" style="top:28px"><svg><use href="#i-home"/></svg>Home</div>
    <div class="nav-divider" style="top:65px"></div>
    <div class="nav-item" style="top:81px"><svg><use href="#i-bell"/></svg>All Alerts</div>
    <div class="nav-divider" style="top:117px"></div>
    <div class="nav-item" style="top:134px"><svg><use href="#i-gear"/></svg>Manage</div>
    <div class="nav-divider" style="top:170px"></div>
    <div class="nav-item" style="top:186px"><svg><use href="#i-horn"/></svg>Campaigns<svg class="end"><use href="#i-plus"/></svg></div>
    <div class="nav-band" style="top:224px"></div>
    <div class="nav-item" style="top:238px"><svg><use href="#i-doc"/></svg>My custom Campaign<svg class="end"><use href="#i-up"/></svg></div>
    <div class="nav-sub nav-sub--soft" style="top:276px"></div>
    <div class="nav-sub-hl" style="top:276px"></div>
    <div class="sub-link" style="top:292px">Overview</div>
    <div class="sub-link" style="top:324px">Files &amp; Honey Tokens</div>
    <div class="sub-link" style="top:355px">Resources</div>
    <div class="sub-link" style="top:387px">Alerts</div>
    <div class="sub-link" style="top:418px">Settings</div>
    <div class="nav-item" style="top:465px"><svg><use href="#i-edit"/></svg>Default Campaign<svg class="end"><use href="#i-down"/></svg></div>
  </nav>

  <div class="section-label" style="left:281px;top:112px">Campaign</div>
  <div class="card card--accent" style="left:281px;top:150px;width:996px;height:98px">
    <div class="circle-icon" style="left:19px;top:19px;width:56px;height:56px"><svg width="38" height="38"><use href="#i-campaign"/></svg></div>
    <div class="abs" style="left:101px;top:22px;font-size:19px">My Custom Campaign</div>
    <div class="abs" style="left:101px;top:52px;font-size:13.5px">This is my custom campaign for finding!</div>
    <div class="btn" style="left:885px;top:28px;width:78px;height:31px">Custom</div>
  </div>

  <div class="section-label" style="left:281px;top:280px">Campaign Organisation</div>
  <div class="card" style="left:281px;top:318px;width:996px;height:108px">
    <div class="circle-icon" style="left:23px;top:24px;width:56px;height:56px"><svg width="32" height="32"><use href="#i-people"/></svg></div>
    <div class="org-text" style="left:99px;top:22px">Self-enabling Deliverables<br>Proprietary Limited<small>Standard</small></div>
    <div class="org-box" style="left:296px;top:22px">86</div>
    <div class="circle-icon" style="left:429px;top:24px;width:56px;height:56px"><svg width="32" height="32"><use href="#i-tree"/></svg></div>
    <div class="org-text" style="left:505px;top:22px">Unleash bleeding-edge<br>Mindhsare<small>11 hours ago</small></div>
    <div class="org-box" style="left:702px;top:22px">8</div>
  </div>

  <div class="section-label" style="left:283px;top:464px">Files &amp; Honey Takens</div>
  <div class="card" style="left:283px;top:500px;width:475px;height:217px">
    <div class="abs" style="left:27px;top:22px;font-size:16px">Statistics</div>
  </div>
  <div class="tile" style="left:312px;top:554px;height:134px"><div class="icon" style="top:20px"><svg width="32" height="32"><use href="#i-tick"/></svg></div><div class="num" style="top:82px">0</div></div>
  <div class="tile" style="left:532px;top:554px;height:134px"><div class="icon" style="top:20px"><svg width="32" height="32"><use href="#i-file"/></svg></div><div class="num" style="top:82px">30</div></div>

  <div class="section-label" style="left:800px;top:464px">Resources</div>
  <div class="card" style="left:800px;top:500px;width:475px;height:217px;text-align:center">
    <div class="circle-icon" style="left:211px;top:42px;width:56px;height:56px"><svg width="34" height="34"><use href="#i-cog"/></svg></div>
    <div class="abs" style="left:0;top:120px;width:100%;font-size:16px;line-height:24px">Generate a collection of fictional organisations,<br>Custom templates, Uploaded files andlogos.</div>
  </div>

  <div class="section-label" style="left:281px;top:753px">Alerts</div>
  <div class="card card--accent" style="left:281px;top:790px;width:996px;height:100px">
    <div class="circle-icon" style="left:19px;top:20px;width:56px;height:56px"><svg width="32" height="32"><use href="#i-alert"/></svg></div>
    <div class="abs" style="left:97px;top:33px;font-size:19px">Alert Statistics will appear here</div>
  </div>

  <div class="copyright" style="top:917px">Copyright © 2023 All Rights Reserved</div>
</section>

</div>
</body>
</html>
```